Presentation for new businessconcept from mediacompany

We have a need of an presentation for our bussinessidea within media.

Attatched is the presentation in text, we need illustrations that shows what we can do in same graphic theme as our logo and site: www.lumiferra.com

As little text as possible since we will use this for presentations but u should still be able to understand every slide without hearing the words.

Please PM me for more info, possible movieproject for same issue will be relevant in beginning of next year as well.

The PelkinTot-bee is right now attatched on the logo so feel free to play with him, just as long we can tell he is the one there :)
Updates

Forget to say, the presentation is going to be in swedish so we will change all the text, please use images only according to the description.

Target Market(s)

People who work with marketing and communication i all kinds of companies.

Industry/Entity Type

Media

Requirements
Must have
• The files we upload is the logo and a rough example of situations we like our pelkintot-bee to be in in the presentation. you are free to come with other suggestions, this is only to give you a hint of what we are looking for.
Please use same colors as we have on www.lumiferra.com
Nice to have
• We would really love it if our Lumiferra Bee were to be an important part in all the slides, like showing, pointing, acting etc in different forms.
Should not have
• We dont want photos or real people, we like it more like a cartoon with our Lumiferra bee as a maincharrachter.

```html
<!DOCTYPE html>
<html lang="en">
<head>
<meta charset="utf-8">
<title>We create heroes! – Lumiferra</title>
<link rel="stylesheet" href="https://fonts.googleapis.com/css2?family=Sniglet&family=Nunito:wght@700;800&display=swap">
<style>
  :root {
    --paper: #efefed;
    --paper-shade: #e6e6e3;
    --spot: #ffffff;
    --lime: #a9c300;
    --olive: #6e7d1f;
    --ink: #7b7b7b;
    --ink-dark: #4a4a4a;
    --hero-red: #d8262a;
    --hero-blue: #3f6fc0;
    --hero-yellow: #f4e21c;
  }
  * { box-sizing: border-box; margin: 0; padding: 0; }
  html, body { width: 1200px; height: 656px; overflow: hidden; }
  body { background: var(--paper); font-family: "Nunito", sans-serif; }

  .slide {
    position: relative;
    width: 1200px;
    height: 656px;
    overflow: hidden;
    background: radial-gradient(circle at 30% 40%, var(--paper) 0%, var(--paper-shade) 100%);
  }

  .spotlight { position: absolute; inset: 0; }

  .title-rule { position: absolute; left: 0; top: 0; }

  .title-mark {
    position: absolute;
    left: 244px; top: 82px;
    width: 18px; height: 18px;
    border-radius: 50%;
    background: var(--olive);
  }

  .slide-title {
    position: absolute;
    left: 310px; top: 52px;
    font-family: "Sniglet", sans-serif;
    font-weight: 400;
    font-size: 40px;
    color: var(--lime);
    letter-spacing: 0.5px;
  }

  .intro {
    position: absolute;
    left: 238px; top: 210px;
    width: 640px;
    font-size: 23px;
    line-height: 31px;
    font-weight: 800;
    color: var(--ink);
  }
  .intro .brand-name { color: var(--ink-dark); }

  .benefits {
    position: absolute;
    left: 300px; top: 354px;
    list-style: none;
  }
  .benefits li {
    display: flex;
    align-items: center;
    height: 36px;
    font-size: 18px;
    font-weight: 700;
    color: var(--lime);
  }
  .benefits li::before {
    content: "";
    width: 12px; height: 12px;
    margin-right: 26px;
    border-radius: 50%;
    background: var(--olive);
  }

  .summary {
    position: absolute;
    left: 238px; top: 446px;
    font-size: 25px;
    font-weight: 800;
    color: var(--ink);
  }

  .hero-figure {
    position: absolute;
    left: 900px; top: 205px;
    width: 300px; height: 250px;
    border-radius: 40% 30% 45% 35%;
    background: linear-gradient(135deg, var(--hero-red) 0%, var(--hero-yellow) 45%, var(--hero-blue) 100%);
    opacity: 0.85;
  }

  .brand-signature {
    position: absolute;
    left: 958px; top: 600px;
    display: flex;
    align-items: center;
    gap: 6px;
    font-family: "Nunito", sans-serif;
    font-size: 20px;
    font-weight: 800;
    color: var(--olive);
  }
  .brand-signature::before {
    content: "";
    width: 10px; height: 10px;
    border-radius: 50%;
    background: var(--olive);
  }
</style>
</head>
<body>
<main class="slide">
  <svg class="spotlight" width="1200" height="656" viewBox="0 0 1200 656" aria-hidden="true">
    <path d="M1200 20 C1020 90 870 240 885 390 C900 520 1050 590 1200 600 Z" fill="var(--spot)"/>
  </svg>

  <svg class="title-rule" width="1200" height="140" viewBox="0 0 1200 140" aria-hidden="true">
    <path d="M268 107 L1020 107 C1032 107 1038 115 1042 126" fill="none" stroke="var(--olive)" stroke-width="3" stroke-linecap="round"/>
  </svg>

  <span class="title-mark" aria-hidden="true"></span>
  <h1 class="slide-title">We create heroes!</h1>

  <p class="intro">By <span class="brand-name">Lumiferra</span> system of " PelkinTots " the customer is offered guaranteed exposures , which makes a PelkinTot for a hero by :</p>

  <ul class="benefits">
    <li>Charity</li>
    <li>Incentives - back to that which divides</li>
  </ul>

  <p class="summary">This focus on increasing loyalty and brand recognition.</p>

  <div class="hero-figure" role="img" aria-label="Cartoon superhero in red mask, blue suit and yellow-red cape flying upward with a raised fist"></div>

  <div class="brand-signature">Lumiferra</div>
</main>
</body>
</html>
```